Dunmore Roofing

Want a professional looking business card

Industry/Entity Type

Business

Contact Information for Business Card

Paul Dunmore ( Owner) paul@dunmoreroofing-example.com, www.dunmoreroofing-example.com, Adress: 4172 Township road 43 Alder Creek,ON K9X4T2

```html
<!DOCTYPE html>
<html lang="en">
<head>
<meta charset="utf-8">
<title>Dunmore Roofing – Business Card</title>
<link href="https://fonts.googleapis.com/css2?family=Roboto+Condensed:wght@700&family=Roboto:wght@400&display=swap" rel="stylesheet">
<style>
  :root {
    --backdrop: #2b2b2b;
    --card-white: #f4f4f4;
    --brand-blue: #173f7c;
    --slate-grey: #707070;
    --ink-white: #ffffff;
  }
  * { margin: 0; padding: 0; box-sizing: border-box; }
  html, body { width: 1200px; height: 960px; overflow: hidden; }
  body {
    background: var(--backdrop);
    font-family: "Roboto", Arial, sans-serif;
    position: relative;
  }
  .card {
    position: absolute;
    width: 600px;
    height: 343px;
    overflow: hidden;
  }
  .card--front { left: 314px; top: 113px; background: var(--card-white); }
  .card--back { left: 311px; top: 472px; background: var(--brand-blue); }

  .holder { position: absolute; left: 42px; top: 44px; }
  .holder__name {
    font-family: "Roboto Condensed", "Arial Narrow", sans-serif;
    font-weight: 700;
    font-size: 24px;
    color: var(--brand-blue);
    letter-spacing: 0.2px;
  }
  .holder__role {
    font-size: 15px;
    color: var(--slate-grey);
    margin-top: 1px;
    letter-spacing: 0.5px;
  }

  .wordmark {
    font-family: "Roboto Condensed", "Arial Narrow", sans-serif;
    font-weight: 700;
    text-align: center;
    line-height: 1;
  }
  .wordmark__main { display: block; }
  .wordmark__sub { display: block; }
  .card--front .wordmark {
    position: absolute; right: 32px; top: 113px; width: 240px; color: var(--brand-blue);
  }
  .card--front .wordmark__main { font-size: 32px; letter-spacing: 11px; margin-right: -11px; }
  .card--front .wordmark__sub { font-size: 15px; letter-spacing: 22px; margin-right: -22px; margin-top: 5px; }
  .card--back .wordmark {
    position: absolute; left: 0; right: 0; top: 180px; color: var(--ink-white);
  }
  .card--back .wordmark__main { font-size: 40px; letter-spacing: 14px; margin-right: -14px; }
  .card--back .wordmark__sub { font-size: 17px; letter-spacing: 26px; margin-right: -26px; margin-top: 8px; }

  .contact-band { position: absolute; left: 0; top: 0; }
  .contact {
    position: absolute;
    right: 32px;
    top: 222px;
    text-align: right;
    color: var(--ink-white);
    font-size: 14.5px;
    line-height: 19px;
  }
  .contact__address { margin-right: 0; margin-bottom: 7px; }
  .contact__line { display: flex; justify-content: flex-end; align-items: center; gap: 6px; }
  .contact__icon { width: 13px; height: 13px; flex: none; }

  .back-url {
    position: absolute; left: 0; right: 0; top: 284px;
    text-align: center;
    color: var(--ink-white);
    font-size: 15px;
    letter-spacing: 4px;
  }
</style>
</head>
<body>

<section class="card card--front" aria-label="Business card front">
  <svg class="contact-band" width="600" height="343" viewBox="0 0 600 343" aria-hidden="true">
    <polygon points="123,205 600,205 600,343 246,343" fill="var(--brand-blue)"/>
  </svg>

  <div class="holder">
    <div class="holder__name">PAUL DUNMORE</div>
    <div class="holder__role">OWNER</div>
  </div>

  <div class="wordmark">
    <span class="wordmark__main">DUNMORE</span>
    <span class="wordmark__sub">ROOFING</span>
  </div>

  <div class="contact">
    <div class="contact__address">4172 Township road 43<br>Alder Creek, ON K9X4T2</div>
    <div class="contact__line">613 555 0147
      <svg class="contact__icon" viewBox="0 0 16 16" aria-hidden="true"><path fill="#fff" d="M3.6 1.2l2.3 2.9-1.3 1.7c.9 2 2.6 3.7 4.6 4.6l1.7-1.3 2.9 2.3-1.3 2.6C7.3 14 2 8.7 1 3.7z"/></svg>
    </div>
    <div class="contact__line">paul@dunmoreroofing-example.com
      <svg class="contact__icon" viewBox="0 0 16 16" aria-hidden="true"><rect x="1" y="3.5" width="14" height="9" fill="#fff"/><path d="M1.5 4l6.5 5 6.5-5" fill="none" stroke="var(--brand-blue)" stroke-width="1.2"/></svg>
    </div>
    <div class="contact__line">www.dunmoreroofing-example.com
      <svg class="contact__icon" viewBox="0 0 16 16" aria-hidden="true"><circle cx="8" cy="8" r="6.5" fill="#fff"/><path d="M5 5.5c1.5 0 2 1.5 3.5 1.5M9 11c0-1.5 1.5-2 2.5-1.5" fill="none" stroke="var(--brand-blue)" stroke-width="1.4"/></svg>
    </div>
  </div>
</section>

<section class="card card--back" aria-label="Business card back">
  <div class="wordmark">
    <span class="wordmark__main">DUNMORE</span>
    <span class="wordmark__sub">ROOFING</span>
  </div>
  <div class="back-url">www.dunmoreroofing-example.com</div>
</section>

</body>
</html>
```